GJ & DW Fencing Pty Ltd

We already have an existing logo created by Pixel Harbour however we have restructured to a company. We would like someone to add Pty Ltd to our business name please.

Colors

Designer to choose only greyscale colors for use in the design.

```html
<!DOCTYPE html>
<html lang="en">
<head>
<meta charset="utf-8">
<title>GJ &amp; DW Fencing Pty Ltd — Business Card</title>
<link rel="stylesheet" href="https://fonts.googleapis.com/css2?family=Montserrat:wght@300;500&family=Playfair+Display+SC:wght@400&display=swap">
<style>
  :root {
    --backdrop: #d9d9d9;
    --card: #fbfbfb;
    --card-edge: #e6e6e6;
    --ink-dark: #3a3a3a;
    --ink-mid: #555555;
    --ink-soft: #6b6b6b;
    --rule: #8a8a8a;
    --icon-bg: #3f3f3f;
    --icon-fg: #ffffff;
  }
  * { margin: 0; padding: 0; box-sizing: border-box; }
  html, body {
    width: 1200px; height: 1022px; overflow: hidden;
    background: var(--backdrop);
  }
  .canvas {
    width: 1200px; height: 1022px;
    display: flex; align-items: center; justify-content: center;
  }
  .business-card {
    width: 900px; height: 514px;
    background: linear-gradient(135deg, var(--card) 0%, #f1f1f1 100%);
    border-radius: 18px;
    border: 1px solid var(--card-edge);
    box-shadow: 0 18px 40px rgba(0,0,0,0.18);
    display: flex; align-items: center;
    padding: 0 70px;
  }
  .brand {
    flex: 0 0 400px;
    display: flex; align-items: center; gap: 18px;
  }
  .brand-dot {
    width: 22px; height: 22px; border-radius: 50%;
    background: var(--ink-dark); flex: none;
  }
  .brand-name {
    font-family: "Montserrat", sans-serif;
    font-weight: 500;
    font-size: 38px;
    line-height: 1.15;
    letter-spacing: 1px;
    color: var(--ink-dark);
    text-transform: uppercase;
  }
  .divider {
    width: 1px; height: 170px;
    background: var(--rule);
    margin: 0 40px 0 20px;
  }
  .contact { display: flex; flex-direction: column; }
  .contact-name {
    font-family: "Playfair Display SC", serif;
    font-size: 30px;
    letter-spacing: 3px;
    color: var(--ink-dark);
    margin-bottom: 18px;
  }
  .contact-list { list-style: none; }
  .contact-item {
    display: flex; align-items: center; gap: 12px;
    font-family: "Montserrat", sans-serif;
    font-weight: 300;
    font-size: 19px;
    color: var(--ink-mid);
    margin-bottom: 10px;
  }
  .contact-icon {
    width: 20px; height: 20px; flex: none;
  }
</style>
</head>
<body>
<main class="canvas">
  <section class="business-card">
    <div class="brand">
      <span class="brand-dot"></span>
      <span class="brand-name">GJ &amp; DW<br>Fencing<br>Pty Ltd</span>
    </div>
    <div class="divider"></div>
    <div class="contact">
      <p class="contact-name">SAM WHITLOCK</p>
      <ul class="contact-list">
        <li class="contact-item">
          <svg class="contact-icon" viewBox="0 0 20 20" aria-hidden="true">
            <circle cx="10" cy="10" r="10" fill="var(--icon-bg)"/>
            <path d="M10 4.5c-2.2 0-3.8 1.6-3.8 3.7 0 2.7 3.8 7 3.8 7s3.8-4.3 3.8-7c0-2.1-1.6-3.7-3.8-3.7z" fill="var(--icon-fg)"/>
            <circle cx="10" cy="8.2" r="1.4" fill="var(--icon-bg)"/>
          </svg>
          PO Box 418 CEDARVALE WA 6512
        </li>
        <li class="contact-item">
          <svg class="contact-icon" viewBox="0 0 20 20" aria-hidden="true">
            <circle cx="10" cy="10" r="10" fill="var(--icon-bg)"/>
            <path d="M6.5 5.5l2 .2.8 2.3-1.2.9c.6 1.3 1.6 2.3 2.9 2.9l.9-1.2 2.3.8.2 2c-.3.6-1 1-1.8 1-3.9-.3-7-3.4-7.3-7.3 0-.8.4-1.5 1.2-1.6z" fill="var(--icon-fg)"/>
          </svg>
          0412 555 019
        </li>
        <li class="contact-item">
          <svg class="contact-icon" viewBox="0 0 20 20" aria-hidden="true">
            <circle cx="10" cy="10" r="10" fill="var(--icon-bg)"/>
            <rect x="5" y="6.5" width="10" height="7" fill="none" stroke="var(--icon-fg)" stroke-width="1.2"/>
            <path d="M5 6.8l5 3.8 5-3.8" fill="none" stroke="var(--icon-fg)" stroke-width="1.2"/>
          </svg>
          gjdwfencing@mailbox.com
        </li>
      </ul>
    </div>
  </section>
</main>
</body>
</html>
```